Spiritual Web Design Project

I am looking to rebrand our www.GentleRiverMentorInstitute.com site to have a more spiritual look and feel (find out everything we do and offer at that site - have also uploaded picture of current site).
Photoshop format is fine and then we can have someone code it for our Wordpress site.
I want the site to have more movement and light to it (but static for our Wordpress site Don't want flash) I want the site to have a warmer, more ethereal feel to it.
I like the yellow, but think it needs more 'life' and a more spiritual feel. I am also thinking of changing to purple (see a sample attached - although this is a little too dark).
Maybe the banner should go the entire width of a webpage (like this): http://www.halvorstudio.com/speaking
or this: http://www.tindrow.com/faqs
with a simple white background
I like this background (but not the dark blue)
http://www.quiet-lantern.com/ I like this style of background, and I like this colour and style here: http://www.meadowpathkits.com/
I want our background to have more 'light and movement' in it.
I am thinking of changing our current font. I quite like the font here:
http://www.quiet-lantern.com/
Also the two fonts attached - I like more depth (light and shade) in these than the one we have on our site now which looks quite flat
I've also attached a sample of some changes I have been looking at but I think there is too much purple
Again, I am not exactly sure what I want, but I will definately know it when I see it. The one thing I would like to keep is our 'flower graphic' on the left hand side. Also, maybe my photo could be incorporated somewhere - but not really sure if it needs to be
Once we have the branding of the site done, I want to re-brand everything else, all the resources, marketing materials etc.
Please don't submit before you look at the sites I have mentioned that I like and the attachments.
ALso I only need the Header Graphic and the Background of the site - we are doing the actual site ourselves - so I need a header and background only
Target Market(s)
Spirit-led women who are looking to start their own Law of Attraction Coaching Business
Industry/Entity Type
Marketing
Requirements
Should not have
- Flash
Should not be dark

```html
<!DOCTYPE html>
<html lang="en">
<head>
<meta charset="utf-8">
<title>Gentle River Mentor Institute</title>
<link href="https://fonts.googleapis.com/css2?family=Cinzel:wght@400;700&family=Cormorant+Garamond:wght@500&family=Arimo:wght@400;700&display=swap" rel="stylesheet">
<style>
:root{
  --purple:#5a3aa6;
  --purple-dark:#3f2a8c;
  --nav-top:#6d4cc4;
  --nav-bottom:#4a2f9c;
  --orange:#e48a12;
  --orange-btn-top:#fbb040;
  --orange-btn-bottom:#ef7f0f;
  --pink-panel:#f6e8f0;
  --grey-panel:#ececec;
  --text:#555;
  --cream:#f3f1e4;
  --footer:#2f2f2f;
  --footer-band:#262626;
  --gold:#f6d46a;
}
*{box-sizing:border-box;margin:0;padding:0}
html,body{width:1200px;height:2211px;overflow:hidden}
body{position:relative;background:var(--cream);font-family:"Arimo",Arial,sans-serif;color:var(--text)}
.abs{position:absolute}
.site-header{left:0;top:0;width:1200px;height:258px;background:linear-gradient(100deg,#fafafa 0%,#f7f3f8 40%,#e6c8ea 62%,#c67fd2 80%,#b566c8 100%)}
.brand-mark{left:90px;top:22px;width:82px;height:82px;background:#f6f0c8;border:1px solid #e4d99a}
.brand-name{left:182px;top:20px;font-family:"Cinzel",serif;font-weight:700;font-size:38px;line-height:42px;color:var(--purple)}
.tagline{left:112px;top:134px;width:480px;font-family:"Cormorant Garamond",serif;font-weight:500;font-size:22px;line-height:30px;color:#777;letter-spacing:.6px}
.main-nav{left:90px;top:264px;width:1020px;height:56px;display:flex;background:linear-gradient(var(--nav-top),var(--nav-bottom));border:1px solid #3b2585}
.main-nav a{display:flex;align-items:center;padding:0 17px;font-family:"Cinzel",serif;font-weight:700;font-size:14.5px;color:#fff;text-decoration:none;border-right:1px solid rgba(255,255,255,.25)}
.main-nav a.current{background:#4030a0}
.content{left:90px;top:325px;width:1020px;height:1578px;background:#fff;box-shadow:0 0 4px rgba(0,0,0,.15)}
.promo{left:98px;top:338px;width:1004px;height:168px;background:linear-gradient(#f5f5f5,#e9e9e9)}
.promo-photo{left:98px;top:338px;width:210px;height:168px;background:linear-gradient(90deg,#e8e8e8,#cfc9c6)}
.promo-title{left:330px;top:358px;width:748px;text-align:right;font-weight:700;font-size:22px;line-height:31px;color:var(--purple)}
.btn-orange{height:44px;display:flex;align-items:center;justify-content:center;font-weight:700;font-size:17px;color:#fff;background:linear-gradient(var(--orange-btn-top),var(--orange-btn-bottom));border:1px solid #d06a06;border-radius:3px}
.lead{left:99px;top:530px;width:650px;font-size:16px;line-height:25px;color:var(--orange)}
.intro{left:99px;top:613px;width:645px;font-size:12.8px;line-height:23px;color:#666}
.btn-grey{left:100px;top:742px;width:115px;height:34px;display:flex;align-items:center;justify-content:center;font-weight:700;font-size:14px;color:#fff;background:linear-gradient(#a8a8a8,#777);border-radius:3px}
.video{left:762px;top:545px;width:336px;height:205px;background:linear-gradient(135deg,#1b1b1b,#3a3430 60%,#1a1a1a);border:4px solid #444}
.guarantee{left:100px;top:805px;width:640px;height:103px;background:var(--gold);border-radius:3px}
.seal{left:100px;top:800px;width:120px;height:114px;background:#e0b23c}
.why{left:99px;top:940px;width:642px;height:335px;background:var(--pink-panel)}
.why h2{position:absolute;left:0;top:14px;width:642px;text-align:center;font-size:30px;color:var(--purple-dark);font-weight:700}
.why ul{position:absolute;left:16px;top:92px;width:610px;list-style:none}
.why li{position:relative;padding-left:26px;font-weight:700;font-size:15px;line-height:23px;color:#333;margin-bottom:19px}
.why li::before{content:"";position:absolute;left:0;top:5px;width:12px;height:12px;border:2px solid #333}
.director{left:100px;top:1295px;width:173px;height:260px;background:linear-gradient(#d7c9b6,#8a7767)}
.caption{left:100px;top:1562px;width:173px;text-align:center;font-size:13px;line-height:19px;color:var(--purple)}
.awards{left:287px;top:1291px;width:470px;list-style:none;font-size:12.6px;line-height:25px;color:#666}
.testimonials{left:99px;top:1630px;width:642px;height:260px;background:var(--pink-panel)}
.testimonials h3{position:absolute;left:16px;top:16px;font-size:21px;color:var(--purple-dark)}
.quote{left:116px;top:1705px;width:460px;font-size:12.8px;line-height:23.4px;color:#666}
.quote-photo{left:589px;top:1712px;width:130px;height:160px;background:linear-gradient(#b78d5d,#5b3c8a)}
.side-panel{background:var(--grey-panel)}
.side-head{text-align:center;font-weight:700;color:var(--purple)}
.module{left:776px;width:312px;height:56px;display:flex;align-items:center;padding-left:46px;padding-right:8px;background:linear-gradient(#a9a9a9,#7b7b7b);border-radius:3px;font-weight:700;font-size:15px;line-height:20px;color:#fff;text-transform:uppercase}
.module::before{content:"";position:absolute;left:13px;top:17px;width:22px;height:22px;border-radius:50%;background:#666}
.module::after{content:"";position:absolute;left:20px;top:24px;width:6px;height:6px;border-top:2px solid #fff;border-right:2px solid #fff;transform:rotate(45deg)}
.badge{top:1776px;height:115px}
.site-footer{left:0;top:1918px;width:1200px;height:243px;background:var(--footer)}
.footer-band{left:0;top:2161px;width:1200px;height:50px;background:var(--footer-band);color:#aaa;font-size:12.5px;text-align:center;line-height:50px}
.footer-title{font-size:17px;color:#eee}
.quick-col{list-style:none;font-size:12px;line-height:29px;color:#ddd}
.quick-col li::before{content:"• ";color:#aaa}
.field{left:628px;width:227px;height:28px;background:#fff;border:1px solid #999;font-size:11px;padding-left:16px;line-height:26px;color:#333}
.submit{left:785px;top:2070px;width:70px;height:28px;background:linear-gradient(#b5b38a,#8a8864);color:#fff;font-weight:700;font-size:14px;text-align:center;line-height:28px}
.social{left:904px;font-size:12.5px;color:#ddd;display:flex;align-items:center;gap:20px}
.social i{display:block;width:26px;height:26px;background:#999}
.social b{font-weight:400;color:#8bb3e8;font-size:14px}
</style>
</head>
<body>
<header class="abs site-header" role="img" aria-label="Soft violet light banner with glowing bokeh">
  <div class="abs brand-mark" role="img" aria-label="Flower emblem"></div>
  <div class="abs brand-name">GENTLE RIVER<br>MENTOR INSTITUTE</div>
  <p class="abs tagline">“ …delivering transformational coach training and business success secrets worldwide ”</p>
</header>

<nav class="abs main-nav">
  <a class="current" href="#">HOME</a>
  <a href="#">LIFE COACH TRAINING</a>
  <a href="#">SUCCESS STORIES</a>
  <a href="#">MEDIA &amp; AWARDS</a>
  <a href="#">CONTACT US</a>
  <a href="#" style="border:0;padding-left:24px">COACHES LOGIN</a>
</nav>

<main>
  <div class="abs content"></div>
  <section class="abs promo"></section>
  <div class="abs promo-photo" role="img" aria-label="Woman with outstretched arms in the breeze"></div>
  <h1 class="abs promo-title">Join Today and Receive an Amazing Bundle of Bonuses, Super Early Bird Pricing and be Ready to Transform Your Life Forever!</h1>
  <a class="abs btn-orange" style="left:517px;top:438px;width:182px">MEMBER LOGIN</a>
  <a class="abs btn-orange" style="left:709px;top:438px;width:180px">JOIN AS COACH</a>
  <a class="abs btn-orange" style="left:894px;top:438px;width:182px">REGISTER NOW</a>

  <p class="abs lead">Do You Love ‘The Quiet Law’ and the Law of Attraction?<br>Want to Spend Your Days Becoming the Best You Can Be?<br>Ready to Help Others Create an AMAZING Future AND be Paid Abundantly to Do So?</p>
  <p class="abs intro">If you answered Yes – then your spirit will soar as you are about to discover how your life will be changed forever more. life coaching training Hi, my name is Maren Ashcombe and I’ve transformed my life and thousands of others by using these exact principles. I became an Accredited Coach in 2001 and have created a wonderfully fulfilling and successful coaching business by combining the Law of Attraction with masterful practical strategies.</p>
  <a class="abs btn-grey">KNOW MORE</a>

  <div class="abs video" role="img" aria-label="Welcome video from the academy director"></div>
  <svg class="abs" style="left:906px;top:625px" width="46" height="46" viewBox="0 0 46 46"><circle cx="23" cy="23" r="21" fill="#888" stroke="#ddd" stroke-width="2"/><path d="M18 13 L33 23 L18 33Z" fill="#fff"/></svg>

  <div class="abs guarantee"></div>
  <div class="abs seal" role="img" aria-label="Satisfaction guarantee seal"></div>
  <h2 class="abs" style="left:240px;top:815px;font-size:23px;color:var(--purple-dark)">OUR 100% SUCCESS GUARANTEE</h2>
  <p class="abs" style="left:242px;top:846px;width:470px;font-size:11px;line-height:18px;font-weight:700;color:#333">Please note: As an GRMI coach, you’ll learn everything you need to create a 6 figure coaching business and results will vary depending on the time and effort you personally put in.</p>

  <section class="abs why">
    <h2>Why Gentle River Mentor Institute</h2>
    <div style="position:absolute;left:14px;top:75px;width:614px;height:1px;background:#cbb6c4"></div>
    <ul>
      <li>In a nutshell, how does the Gentle River Coach Certification program work?</li>
      <li>The Gentle River Mentor Institute Certification Program offers</li>
      <li>Internationally Certified Gentle River Coach</li>
      <li>On completion of your training, you’ll receive Professional Credentials as an Gentle River Coach (and can call yourself a Certified Gentle River Coach OR a Certified Gentle River Law of Attraction Coach) for added credibility.</li>
    </ul>
  </section>

  <div class="abs director" role="img" aria-label="Portrait of the academy director"></div>
  <p class="abs caption">Gentle River Mentor Institute Director</p>
  <ul class="abs awards">
    <li>Winner – 2012 Bronze Award Mentor or Coach of the Year – New York</li>
    <li>Winner – 2012 Bronze Award Female Entrepreneur of the Year – New York</li>
    <li>Winner – 2010 Best Overall Company of the Year – New York</li>
    <li>Finalist – 2010 Entrepreneur of the Year – New York</li>
    <li>Winner – 2010 Business of the Year – Australia</li>
    <li>Finalist – 2010 Excellence in Business – Australia</li>
    <li>Finalist – 2009 Women Helping Women – New York</li>
    <li>Winner – 2008 Mentor of the Year – New York</li>
    <li>Finalist – 2008 Marketing and Communications Awards – Australia</li>
    <li>Finalist – 2008 Overall Business of the Year – New York</li>
    <li>Finalist – 2007 Business Woman of the Year – New York</li>
    <li>Winner – 2005 Australian Micro Business Award – Australia</li>
    <li>International Prosperity and Success Coach</li>
  </ul>

  <section class="abs testimonials">
    <h3>Testimonials</h3>
    <svg style="position:absolute;left:596px;top:20px" width="28" height="18" viewBox="0 0 28 18"><path d="M9 2 L3 9 L9 16 M19 2 L25 9 L19 16" fill="none" stroke="#333" stroke-width="2.5"/></svg>
    <div style="position:absolute;left:14px;top:58px;width:614px;height:1px;background:#d6c3cf"></div>
  </section>
  <p class="abs quote">“I love the spiritual content of the program and the practicality of the course. I love the power and freedom I feel within; the joy and ease of supporting other people. Maren and the GRMI helped me to rediscover the great person within and have given me back my confidence to do things I didn’t think I could do. From the very depths of my heart thank you very much Maren for making a difference in my life”.<br><b style="display:block;margin-top:10px;color:var(--purple-dark)">Maren A., Australia</b></p>
  <div class="abs quote-photo" role="img" aria-label="Graduate with the director"></div>

  <section class="abs side-panel" style="left:762px;top:795px;width:336px;height:463px"></section>
  <p class="abs side-head" style="left:776px;top:806px;width:310px;font-size:16.5px;line-height:23px">Students in the Gentle River Mentor Institute will be guided through 6 modules:</p>
  <div class="abs module" style="top:886px">Masterful Coaching Skills for Success</div>
  <div class="abs module" style="top:946px">The Quiet Law Behind The Quiet Law</div>
  <div class="abs module" style="top:1007px">Blissful Business Building &amp; The Magic of Marketing</div>
  <div class="abs module" style="top:1067px">Million Dollar Mindset Secrets</div>
  <div class="abs module" style="top:1128px">Transformational Energy Processes</div>
  <div class="abs module" style="top:1188px">Advanced Divine Manifesting</div>

  <section class="abs side-panel" style="left:762px;top:1265px;width:336px;height:497px"></section>
  <p class="abs side-head" style="left:776px;top:1277px;width:310px;font-size:14px">Limited Places – Secure your Place NOW!</p>
  <p class="abs side-head" style="left:776px;top:1303px;width:310px;font-size:16.5px;line-height:23px">Say YES today and receive the following BONUS package</p>
  <p class="abs side-head" style="left:776px;top:1356px;width:310px;font-size:16.5px;color:var(--orange)">Valued at over $4700 – Yours FREE!</p>
  <div class="abs module" style="top:1391px">Millionaire Mindset Mentoring Home-Study</div>
  <div class="abs module" style="top:1452px">How to be Wildly Wealthy Fast – 20 Copies</div>
  <div class="abs module" style="top:1512px">Transformational Subliminal Audios – 70 CDs</div>
  <div class="abs module" style="top:1573px">Group Coaching Success Secrets</div>
  <div class="abs module" style="top:1633px">Your Own Coaching Website and Product</div>
  <div class="abs module" style="top:1694px">Week Coaching Program</div>

  <div class="abs badge" style="left:764px;width:88px;background:#e9e4d4;border:2px solid #1e5a6a"></div>
  <div class="abs badge" style="left:864px;width:82px;background:linear-gradient(#1c8aa0,#12395a)"></div>
  <div class="abs badge" style="left:952px;width:90px;background:linear-gradient(#f6e6ea,#d8b0a0)"></div>
  <div class="abs badge" style="left:1018px;top:1848px;width:74px;height:42px;background:#f2f2f2;border:1px solid #ccc"></div>
</main>

<footer>
  <div class="abs site-footer"></div>
  <div class="abs footer-title" style="left:92px;top:1940px">Quick Links</div>
  <ul class="abs quick-col" style="left:94px;top:1974px"><li>Integer lobortis</li><li>Curabitur ac</li><li>Phasellus tellus nisl</li><li>Aenean fringilla</li><li>Vestibulum</li><li>Aliquam commodo</li></ul>
  <ul class="abs quick-col" style="left:272px;top:1974px"><li>Integer lobortis</li><li>Curabitur ac</li><li>Phasellus tellus nisl</li><li>Aenean fringilla</li><li>Vestibulum</li><li>Aliquam commodo</li></ul>
  <ul class="abs quick-col" style="left:452px;top:1974px"><li>Integer lobortis</li><li>Curabitur ac</li><li>Phasellus tellus nisl</li><li>Aenean fringilla</li><li>Vestibulum</li><li>Aliquam commodo</li></ul>
  <div class="abs" style="left:601px;top:1938px;width:1px;height:200px;background:#555"></div>
  <div class="abs footer-title" style="left:628px;top:1940px">Email Signup</div>
  <div class="abs field" style="top:1984px">Name</div>
  <div class="abs field" style="top:2026px">Email ID</div>
  <div class="abs submit">SUBMIT</div>
  <div class="abs" style="left:877px;top:1938px;width:1px;height:200px;background:#555"></div>
  <div class="abs footer-title" style="left:904px;top:1940px">Connect with us</div>
  <div class="abs social" style="top:1983px"><i></i><span>Join with us on <b>Friendlane</b></span></div>
  <div class="abs social" style="top:2025px"><i></i><span>Follow us on <b>Chirpline</b></span></div>
  <div class="abs social" style="top:2067px"><i></i><span>Share on <b>Worknest</b></span></div>
  <div class="abs social" style="top:2109px"><i></i><span>Watch on <b style="color:#fff">Reelhouse</b></span></div>
  <div class="abs footer-band">Copyright © 2013 &nbsp; www.gentlerivermentorinstitute.com &nbsp; All rights reserved.</div>
</footer>
</body>
</html>
```